Simple and Clean business card design

We would like the design to be simple clean and to incorporate our colors.

We are open to your design and talent, we have the dots in our logo as we think of it as data points and we connect data points for people.

We are open to see the great creative and clean design you bring to the table

Contact Information for Business Card

please include: name, position, email, phone and website

Font styles to use
Sans Serif

Requirements
Must have
• my colors incorporated, simplicity
Nice to have
• lots of white space, simplicity
Should not have
• complexicity/ complex art

```html
<!DOCTYPE html>
<html lang="en">
<head>
<meta charset="utf-8">
<title>Brio Business Card</title>
<link href="https://fonts.googleapis.com/css2?family=Lato:wght@400;700;900&display=swap" rel="stylesheet">
<style>
  :root {
    --bg: #2b2b2c;
    --card: #1b1c1e;
    --pattern-light: #5a5a5c;
    --pattern-mid: #2e2e30;
    --pattern-dark: #141416;
    --white: #ffffff;
    --blue: #4285f4;
    --rule: #4a4b4e;
  }
  * { box-sizing: border-box; margin: 0; padding: 0; }
  html, body {
    width: 1200px;
    height: 1108px;
    overflow: hidden;
    background: var(--bg);
    font-family: "Lato", Arial, sans-serif;
  }
  .stage {
    position: relative;
    width: 1200px;
    height: 1108px;
  }
  .card {
    position: absolute;
    top: 214px;
    width: 400px;
    height: 680px;
    border-radius: 26px;
    background: var(--card);
    overflow: hidden;
    box-shadow: 0 18px 40px rgba(0,0,0,0.45);
  }
  .card--front { left: 170px; }
  .card--back { left: 630px; }

  .wordmark {
    position: absolute;
    color: var(--white);
    font-weight: 900;
    letter-spacing: -1px;
    line-height: 1;
  }
  .card--front .wordmark {
    top: 140px;
    left: 0;
    right: 0;
    text-align: center;
    font-size: 104px;
  }

  .contact {
    position: absolute;
    left: 0;
    right: 0;
    top: 420px;
    text-align: center;
    color: var(--white);
  }
  .contact__name {
    color: var(--blue);
    font-size: 30px;
    font-weight: 700;
    letter-spacing: 0.5px;
  }
  .contact__role {
    font-size: 20px;
    margin-top: 4px;
  }
  .contact__icons {
    display: flex;
    align-items: center;
    justify-content: center;
    gap: 8px;
    margin: 18px 0 14px;
  }
  .contact__rule {
    width: 38px;
    height: 1px;
    background: var(--rule);
  }
  .contact__icons svg { width: 30px; height: 30px; }
  .contact__line {
    font-size: 19px;
    line-height: 1.45;
  }

  .card__pattern {
    position: absolute;
    inset: 0;
    background:
      radial-gradient(ellipse at 85% 5%, var(--pattern-light) 0%, rgba(90,90,92,0) 55%),
      linear-gradient(200deg, #3c3c3e 0%, var(--pattern-mid) 40%, var(--pattern-dark) 80%);
  }
  .card--back .wordmark {
    right: 40px;
    bottom: 110px;
    font-size: 84px;
  }
</style>
</head>
<body>
<main class="stage">
  <section class="card card--front">
    <div class="wordmark">Brio</div>
    <div class="contact">
      <p class="contact__name">DANA WELLES</p>
      <p class="contact__role">Founder/ CEO</p>
      <div class="contact__icons">
        <span class="contact__rule"></span>
        <svg viewBox="0 0 30 30" aria-label="Phone">
          <circle cx="15" cy="15" r="13" fill="none" stroke="var(--blue)" stroke-width="2.5"/>
          <path d="M11 9 l3 0 1 4 -2 1.5 a8 8 0 0 0 3.5 3.5 l1.5 -2 4 1 0 3 a1.5 1.5 0 0 1 -1.5 1.5 A11 11 0 0 1 9.5 10.5 A1.5 1.5 0 0 1 11 9z" fill="var(--blue)"/>
        </svg>
        <svg viewBox="0 0 30 30" aria-label="Email">
          <circle cx="15" cy="15" r="13" fill="none" stroke="var(--blue)" stroke-width="2.5"/>
          <rect x="8" y="10" width="14" height="10" fill="none" stroke="var(--blue)" stroke-width="2"/>
          <path d="M8 10 l7 6 7 -6" fill="none" stroke="var(--blue)" stroke-width="2"/>
        </svg>
        <svg viewBox="0 0 30 30" aria-label="Website">
          <circle cx="15" cy="15" r="13" fill="none" stroke="var(--blue)" stroke-width="2.5"/>
          <circle cx="15" cy="15" r="7.5" fill="none" stroke="var(--blue)" stroke-width="1.6"/>
          <ellipse cx="15" cy="15" rx="3.2" ry="7.5" fill="none" stroke="var(--blue)" stroke-width="1.4"/>
          <path d="M7.5 15 h15 M9 11 h12 M9 19 h12" stroke="var(--blue)" stroke-width="1.4"/>
        </svg>
        <span class="contact__rule"></span>
      </div>
      <p class="contact__line">555-204-1187</p>
      <p class="contact__line">dana.welles@brio.one</p>
      <p class="contact__line">www.Brio.one</p>
    </div>
  </section>

  <section class="card card--back">
    <div class="card__pattern" role="img" aria-label="Decorative pattern of grey dots and rings in diagonal rows, light grey at the top right fading to near black at the bottom"></div>
    <div class="wordmark">Brio</div>
  </section>
</main>
</body>
</html>
```